Verdel Harvest - Stationery Design Project

We need a stationary for our business. We grow roots and fruits in Central and South America, we import and distribute in FL, USA. We do fresh and frozen products.

Target Market(s)

Small and big supermarkets, wholesalers, traders, distributors, etc

Industry/Entity Type

Business

```html
<!DOCTYPE html>
<html lang="en">
<head>
<meta charset="utf-8">
<title>Verdel Harvest – Stationery</title>
<link rel="stylesheet" href="https://fonts.googleapis.com/css2?family=Montserrat:wght@500&display=swap">
<style>
  :root {
    --backdrop: #e6e6e4;
    --paper: #f8f8f8;
    --leaf-green: #546434;
    --harvest-orange: #e8830c;
    --ink-grey: #7a7a7a;
  }
  * { margin: 0; padding: 0; box-sizing: border-box; }
  html, body { width: 1200px; height: 1000px; overflow: hidden; }
  body {
    background: var(--backdrop);
    font-family: "Montserrat", Arial, sans-serif;
    position: relative;
  }
  .sheet { position: absolute; background: var(--paper); overflow: hidden; }
  .brand-name {
    position: absolute;
    font-weight: 500;
    white-space: nowrap;
    line-height: 1;
    color: var(--leaf-green);
  }

  /* Presentation folder */
  .folder { left: 190px; top: 108px; width: 385px; height: 543px; }
  .folder-spine { position: absolute; left: 0; top: 0; width: 14px; height: 100%; background: var(--leaf-green); }
  .folder .brand-name { left: 0; right: 0; top: 358px; text-align: center; font-size: 34px; padding-left: 14px; }

  /* Letterhead */
  .letterhead { left: 610px; top: 123px; width: 375px; height: 528px; }
  .letterhead .brand-name { left: 20px; top: 38px; font-size: 16px; }
  .letterhead-rule { position: absolute; left: 0; top: 83px; width: 100%; height: 2px; background: var(--leaf-green); }
  .letterhead-footer { position: absolute; left: 0; bottom: 0; width: 100%; height: 16px; background: var(--leaf-green); }
  .contact-list { position: absolute; left: 242px; top: 31px; list-style: none; }
  .contact-list li {
    display: flex; align-items: center; gap: 8px;
    font-size: 6.5px; color: var(--ink-grey); height: 11.5px;
  }
  .contact-list li:first-child { font-size: 8px; }
  .contact-dot { width: 7px; height: 7px; border-radius: 50%; background: var(--leaf-green); flex: none; }

  /* Envelope */
  .envelope { left: 190px; top: 698px; width: 392px; height: 193px; }
  .envelope-flap { position: absolute; left: 0; top: 0; }
  .envelope .brand-name { left: 0; right: 0; top: 22px; text-align: center; font-size: 11px; color: var(--paper); }

  /* Compliment card */
  .compliment-card { left: 618px; top: 698px; width: 392px; height: 193px; }
  .compliment-card .brand-name { right: 16px; top: 26px; font-size: 10px; }
  .card-footer { position: absolute; left: 0; bottom: 0; width: 100%; height: 15px; background: var(--leaf-green); }
</style>
</head>
<body>

  <section class="sheet folder" aria-label="Presentation folder">
    <div class="folder-spine"></div>
    <p class="brand-name">Verdel Harvest</p>
  </section>

  <section class="sheet letterhead" aria-label="Letterhead">
    <p class="brand-name">Verdel Harvest</p>
    <ul class="contact-list">
      <li><span class="contact-dot"></span>0400 555 182</li>
      <li><span class="contact-dot"></span>support@verdelharvest.com</li>
      <li><span class="contact-dot"></span>www.verdelharvest.com</li>
    </ul>
    <div class="letterhead-rule"></div>
    <div class="letterhead-footer"></div>
  </section>

  <section class="sheet envelope" aria-label="Envelope">
    <svg class="envelope-flap" width="392" height="57" viewBox="0 0 392 57" aria-hidden="true">
      <path d="M0 0 H392 L389 38 Q387 55 368 57 H24 Q5 55 3 38 Z" fill="var(--leaf-green)"/>
    </svg>
    <p class="brand-name">Verdel Harvest</p>
  </section>

  <section class="sheet compliment-card" aria-label="Compliment card">
    <p class="brand-name">Verdel Harvest</p>
    <div class="card-footer"></div>
  </section>

</body>
</html>
```